Looking for a cool & simple business-card-design for digital agency

Hi!

We are a web agency that offers Reputation Management, Vextor & Seo Services and software development. We like cool things, we like innovative styles.

We have uploaded our logo.

Project Deadline Extended Reason: Client does not want any designs with the colorful logo. Please send us submissions ONLY with the blac and white logo. What the client would like to see:1) Back of the card: is a silver logo on a black background2) front of the card with all the data, please use white background and black logo thank you Added Friday, May 8, 2015

Industry/Entity Type

Software

```html
<!DOCTYPE html>
<html lang="en">
<head>
<meta charset="utf-8">
<title>Nordvale business card</title>
<link rel="stylesheet" href="https://fonts.googleapis.com/css2?family=Open+Sans:wght@400;600;700&display=swap">
<style>
  :root {
    --backdrop: #d9d9d9;
    --card-black: #111111;
    --card-black-edge: #2a2a2a;
    --card-white: #ffffff;
    --silver: #d4d4d4;
    --ink: #1e1e1e;
    --ink-soft: #6a6a6a;
    --stripe-grey: #c8c8c8;
  }
  * { box-sizing: border-box; margin: 0; padding: 0; }
  html, body { width: 1200px; height: 852px; overflow: hidden; }
  body {
    background: var(--backdrop);
    font-family: "Open Sans", Arial, sans-serif;
    position: relative;
  }
  .card {
    position: absolute;
    width: 500px;
    height: 286px;
    border-radius: 12px;
    overflow: hidden;
    box-shadow: 0 10px 24px rgba(0,0,0,0.22);
  }
  .card-back {
    left: 110px;
    top: 150px;
    background: linear-gradient(135deg, var(--card-black-edge) 0%, var(--card-black) 55%, #050505 100%);
    display: flex;
    align-items: center;
    justify-content: center;
  }
  .brand {
    display: flex;
    align-items: center;
    gap: 12px;
    font-weight: 700;
    letter-spacing: 1px;
  }
  .brand-mark {
    width: 34px;
    height: 34px;
  }
  .card-back .brand { color: var(--silver); font-size: 46px; }
  .card-back .brand-mark { background: var(--silver); }

  .card-front {
    left: 600px;
    top: 430px;
    background: var(--card-white);
  }
  .side-band {
    position: absolute;
    left: 0; top: 0; bottom: 0;
    width: 36px;
    background: var(--card-black);
  }
  .side-stripe {
    position: absolute;
    left: 36px; top: 0; bottom: 0;
    width: 6px;
    background: var(--stripe-grey);
  }
  .front-content {
    position: absolute;
    left: 66px;
    top: 34px;
    right: 24px;
  }
  .card-front .brand { color: var(--ink); font-size: 40px; }
  .card-front .brand-mark { background: var(--ink); width: 30px; height: 30px; }
  .person { margin-top: 26px; }
  .person-name { font-size: 15px; font-weight: 700; color: var(--ink); }
  .person-role { font-size: 10px; color: var(--ink-soft); margin-top: 1px; }
  .contact-list { list-style: none; margin-top: 14px; }
  .contact-list li {
    display: flex;
    align-items: center;
    gap: 8px;
    font-size: 12px;
    color: var(--ink);
    line-height: 18px;
  }
  .contact-list svg { width: 11px; height: 11px; fill: var(--ink); flex: none; }
  .contact-list .indent { padding-left: 19px; }
</style>
</head>
<body>
  <section class="card card-back" aria-label="Card back">
    <div class="brand"><span class="brand-mark"></span>Nordvale</div>
  </section>

  <section class="card card-front" aria-label="Card front">
    <div class="side-band"></div>
    <div class="side-stripe"></div>
    <div class="front-content">
      <div class="brand"><span class="brand-mark"></span>Nordvale</div>
      <div class="person">
        <p class="person-name">Your Long Name</p>
        <p class="person-role">Managing Director</p>
      </div>
      <ul class="contact-list">
        <li>
          <svg viewBox="0 0 12 12"><path d="M6 0a4 4 0 0 0-4 4c0 3 4 8 4 8s4-5 4-8a4 4 0 0 0-4-4zm0 5.6A1.6 1.6 0 1 1 6 2.4a1.6 1.6 0 0 1 0 3.2z"/></svg>
          Your Commercial or office address
        </li>
        <li class="indent">00.00.00.0000 &nbsp;&#9632; 00.00.00.0000</li>
        <li>
          <svg viewBox="0 0 12 12"><path d="M2.5 0.5l2 2.5-1.2 1.4a7 7 0 0 0 4.3 4.3L9 7.5l2.5 2-1.5 2C5 11.5 0.5 7 0.5 2z"/></svg>
          yourname@yourwebsite.com
        </li>
        <li>
          <svg viewBox="0 0 12 12"><path d="M0 2h12v8H0z M0 2l6 4.5L12 2" stroke="#fff" stroke-width="0.8"/></svg>
          www.yourwebsite.com
        </li>
        <li>
          <svg viewBox="0 0 12 12"><circle cx="6" cy="6" r="5.5"/><path d="M0.5 6h11M6 0.5v11" stroke="#fff" stroke-width="0.7"/></svg>
          www.yourwebsite.com
        </li>
      </ul>
    </div>
  </section>
</body>
</html>
```